Meridale Real Estate

We are looking for help with web design for a new company that is revolutionizing the real estate world on the listing side: by charing per hour for top level professional real estate services. We would like the concept to be simple, clean and easily understood.
Updates

We want this website to actually function, not just a static design.

Industry/Entity Type

Real Estate

```html
<!DOCTYPE html>
<html lang="en">
<head>
<meta charset="utf-8">
<title>Meridale Real Estate</title>
<link href="https://fonts.googleapis.com/css2?family=Open+Sans:wght@300;400;600;700&display=swap" rel="stylesheet">
<style>
:root{
  --bg:#000;
  --footer:#151515;
  --blue:#1e9fdc;
  --blue-light:#3cb8ec;
  --blue-dark:#168bd3;
  --white:#fff;
  --text:#e6e6e6;
  --muted:#cfcfcf;
  --caption:rgba(38,38,40,.9);
}
*{margin:0;padding:0;box-sizing:border-box}
html,body{width:747px;height:1200px;overflow:hidden;background:var(--bg)}
body{font-family:"Open Sans",Arial,sans-serif;color:var(--text);position:relative}
a{color:inherit;text-decoration:none}
.abs{position:absolute}

/* brand */
.brand{display:flex;align-items:center;gap:7px;color:var(--blue);font-weight:600;letter-spacing:.5px}
.brand-dot{border:2px solid var(--blue);border-radius:50%}
.site-brand{left:0;width:747px;top:30px;justify-content:center;font-size:15px}
.site-brand .brand-dot{width:28px;height:28px}

/* nav */
.main-nav{left:103px;top:93px;width:541px;height:37px;display:flex;
  background:linear-gradient(var(--blue-light),var(--blue-dark))}
.main-nav a{display:flex;align-items:center;justify-content:center;color:var(--white);
  font-size:10.5px;font-weight:600;border-right:1px solid rgba(255,255,255,.25)}
.main-nav a:last-child{border-right:0}

/* hero */
.hero{left:103px;top:140px;width:541px;height:209px;
  background:linear-gradient(100deg,#1f3f9e 0%,#3d6fd0 35%,#8fc0ec 55%,#7fb94a 72%,#d8e86a 100%)}
.hero-caption{left:124px;top:238px;width:201px;height:78px;background:var(--caption);padding:16px 14px}
.hero-caption h1{font-size:19px;font-weight:600;color:var(--white);line-height:1.1}
.hero-caption p{font-size:11px;font-weight:300;color:var(--white);margin-top:4px}
.hero-dots{left:350px;top:327px;display:flex;gap:3px}
.hero-dots span{width:9px;height:9px;border-radius:50%;background:#000}
.hero-dots span:first-child{background:#fff}

/* headings */
.section-title{font-size:11px;font-weight:700;color:var(--blue)}
.pager{display:flex;gap:6px}
.pager svg{width:7px;height:12px}

/* categories */
.category-img{height:68px}
.category-label{font-size:8.5px;font-weight:700;color:var(--white);display:flex;justify-content:space-between;align-items:center}
.category-label i{width:11px;height:11px;border-radius:50%;background:var(--blue);display:flex;align-items:center;justify-content:center}

/* listings */
.listing{width:130px}
.listing-img{height:86px;width:127px}
.listing h3{font-size:11.5px;font-weight:300;color:var(--white);margin-top:9px;line-height:1.2}
.listing .dev{font-size:8px;font-weight:700;color:var(--white);margin:2px 0 0 3px}
.listing .price{font-size:9.5px;font-weight:600;color:var(--blue);margin-top:2px}
.listing .loc{font-size:8px;font-weight:700;color:var(--white);margin-top:2px}
.listing .actions{display:flex;gap:8px;margin-top:7px}
.btn{height:20px;display:flex;align-items:center;justify-content:center;font-size:8.5px;font-weight:600;
  color:var(--white);background:linear-gradient(var(--blue-light),var(--blue-dark));border-radius:2px}

/* news */
.news{width:172px}
.news-img{height:92px}
.news p{font-size:8px;line-height:14px;color:var(--muted);margin-top:12px}
.news .more{display:block;font-size:8px;font-weight:700;color:var(--white);margin-top:7px}

.gallery{left:472px;top:804px;width:171px;height:156px;
  background:linear-gradient(180deg,#2f5d8a 0%,#4c7da8 40%,#3b6b4a 80%,#2c4d2c 100%)}
.gallery-caption{left:472px;top:936px;width:171px;height:24px;background:rgba(20,30,20,.6);
  font-size:8px;font-weight:600;color:var(--white);padding:6px 7px}
.gallery-arrow{top:858px;width:14px;height:24px}

/* footer */
.site-footer{left:0;top:1002px;width:747px;height:198px;background:var(--footer)}
.footer-brand{left:108px;top:1038px;flex-direction:column;gap:4px;font-size:8.5px;text-align:center;width:84px}
.footer-brand .brand-dot{width:22px;height:22px}
.footer-divider{left:193px;top:1010px;width:2px;height:150px;background:linear-gradient(#151515,#050505 50%,#151515)}
.footer-links{list-style:none;font-size:8px;color:var(--muted)}
.footer-links li{height:19.5px}
.contact{font-size:7px;color:var(--muted);line-height:13.5px}
.contact strong{font-size:8px;color:var(--white);display:block;margin-bottom:1px}
.connect h4{font-size:8px;color:var(--white);font-weight:700}
.social{display:flex;gap:4px;margin-top:12px}
.social span{width:20px;height:20px;border-radius:50%;background:var(--blue)}
.copyright{left:0;width:747px;top:1171px;text-align:center;font-size:6.5px;font-weight:700;color:var(--muted)}
</style>
</head>
<body>

<div class="abs brand site-brand"><span class="brand-dot"></span>Meridale Real Estate</div>

<nav class="abs main-nav">
  <a href="#" style="width:71px">Home</a>
  <a href="#" style="width:105px">Commercial</a>
  <a href="#" style="width:99px">Residential</a>
  <a href="#" style="width:62px">Farm</a>
  <a href="#" style="width:106px">Vacant Land</a>
  <a href="#" style="width:98px">Contact</a>
</nav>

<div class="abs hero" role="img" aria-label="Glass office tower against blue sky beside a sunlit green tree"></div>
<div class="abs hero-caption"><h1>We deal with both</h1><p>residential and commercial sales</p></div>
<div class="abs hero-dots"><span></span><span></span><span></span><span></span></div>

<h2 class="abs section-title" style="left:0;width:747px;text-align:center;top:379px">What We Sell</h2>

<div class="abs category-img" style="left:102px;top:409px;width:128px;background:linear-gradient(#8fb37a,#2f5a2a 60%,#d9d9d6)" role="img" aria-label="White luxury home among trees"></div>
<div class="abs category-img" style="left:242px;top:409px;width:124px;background:linear-gradient(160deg,#1a2330,#4b5f78 60%,#20262e)" role="img" aria-label="Office building facade"></div>
<div class="abs category-img" style="left:383px;top:409px;width:123px;background:linear-gradient(#2b3036,#3c4129 55%,#283219)" role="img" aria-label="Farmhouse on open field at dusk"></div>
<div class="abs category-img" style="left:521px;top:409px;width:123px;background:linear-gradient(#1c2a3c,#243a2a 60%,#1a2f16)" role="img" aria-label="Fenced ranch pasture"></div>

<div class="abs category-label" style="left:101px;top:483px;width:128px">Luxury homes<i><svg width="6" height="6" viewBox="0 0 6 6"><path d="M2 1l2 2-2 2" stroke="#fff" stroke-width="1.3" fill="none"/></svg></i></div>
<div class="abs category-label" style="left:240px;top:483px;width:126px">Office Buildings<i><svg width="6" height="6" viewBox="0 0 6 6"><path d="M2 1l2 2-2 2" stroke="#fff" stroke-width="1.3" fill="none"/></svg></i></div>
<div class="abs category-label" style="left:383px;top:483px;width:125px">Farms<i><svg width="6" height="6" viewBox="0 0 6 6"><path d="M2 1l2 2-2 2" stroke="#fff" stroke-width="1.3" fill="none"/></svg></i></div>
<div class="abs category-label" style="left:519px;top:483px;width:125px">Ranches<i><svg width="6" height="6" viewBox="0 0 6 6"><path d="M2 1l2 2-2 2" stroke="#fff" stroke-width="1.3" fill="none"/></svg></i></div>

<h2 class="abs section-title" style="left:103px;top:529px">Luxury Homes</h2>
<div class="abs pager" style="left:622px;top:530px">
  <svg viewBox="0 0 7 12"><path d="M6 1L1.5 6 6 11" stroke="#fff" stroke-width="2" fill="none"/></svg>
  <svg viewBox="0 0 7 12"><path d="M1 1l4.5 5L1 11" stroke="#fff" stroke-width="2" fill="none"/></svg>
</div>

<article class="abs listing" style="left:103px;top:556px">
  <div class="listing-img" style="background:linear-gradient(#8fb0d8,#3c6fa0 50%,#14425e)" role="img" aria-label="Villa with infinity pool overlooking water"></div>
  <h3>Halden Villa Grande</h3><p class="dev">by Halden Developers</p>
  <p class="price">$248,298.394 .00 Onwards</p><p class="loc">Brookvale, Newyork</p>
  <div class="actions"><a class="btn" style="width:56px;margin-left:-1px" href="#">Buy Now</a><a class="btn" style="width:58px" href="#">View Details</a></div>
</article>
<article class="abs listing" style="left:241px;top:556px">
  <div class="listing-img" style="background:linear-gradient(#1b3d6e,#2d6b9e 55%,#16304a)" role="img" aria-label="Resort villa pool at twilight with palms"></div>
  <h3>Halden Villa Grande</h3><p class="dev">by Halden Developers</p>
  <p class="price">$248,298.394 .00 Onwards</p><p class="loc">Brookvale, Newyork</p>
  <div class="actions"><a class="btn" style="width:58px" href="#">Buy Now</a><a class="btn" style="width:58px" href="#">View Details</a></div>
</article>
<article class="abs listing" style="left:383px;top:556px">
  <div class="listing-img" style="background:linear-gradient(#d9d6d0,#6e5a44 50%,#2f2a22)" role="img" aria-label="Stone and timber mountain home beside a stream"></div>
  <h3>Halden Villa Grande</h3><p class="dev">by Halden Developers</p>
  <p class="price">$248,298.394 .00 Onwards</p><p class="loc">Brookvale, Newyork</p>
  <div class="actions"><a class="btn" style="width:58px" href="#">Buy Now</a><a class="btn" style="width:58px" href="#">View Details</a></div>
</article>
<article class="abs listing" style="left:518px;top:556px">
  <div class="listing-img" style="background:linear-gradient(#2e5fb0,#9ab7d8 55%,#9b9a8e)" role="img" aria-label="Modern white house on a hillside"></div>
  <h3>Halden Villa Grande</h3><p class="dev">by Halden Developers</p>
  <p class="price">$248,298.394 .00 Onwards</p><p class="loc">Brookvale, Newyork</p>
  <div class="actions"><a class="btn" style="width:58px" href="#">Buy Now</a><a class="btn" style="width:58px" href="#">View Details</a></div>
</article>

<h2 class="abs section-title" style="left:103px;top:781px">Latest News</h2>
<div class="abs pager" style="left:440px;top:783px">
  <svg viewBox="0 0 7 12"><path d="M6 1L1.5 6 6 11" stroke="#fff" stroke-width="2" fill="none"/></svg>
  <svg viewBox="0 0 7 12"><path d="M1 1l4.5 5L1 11" stroke="#fff" stroke-width="2" fill="none"/></svg>
</div>
<h2 class="abs section-title" style="left:472px;top:781px">Photo Gallery</h2>

<article class="abs news" style="left:103px;top:804px">
  <div class="news-img" style="background:linear-gradient(#3a6fb8,#a7b9c7 50%,#4e6b34)" role="img" aria-label="Suburban family house with lawn"></div>
  <p>Lorem Ipsum is simply dummy text of the printing and typesetting industry. Lorem Ipsum has been the industry's standard</p>
  <a class="more" href="#">Read More</a>
</article>
<article class="abs news" style="left:287px;top:804px">
  <div class="news-img" style="background:linear-gradient(#1c2f58,#3a5a86 50%,#1a1f26)" role="img" aria-label="Lit office building at dusk"></div>
  <p>Lorem Ipsum is simply dummy text of the printing and typesetting industry. Lorem Ipsum has been the industry's standard</p>
  <a class="more" href="#">Read More</a>
</article>

<div class="abs gallery" role="img" aria-label="Glass office building behind trees and lawn"></div>
<svg class="abs gallery-arrow" style="left:484px" viewBox="0 0 14 24"><path d="M12 2L3 12l9 10" stroke="#fff" stroke-width="3.5" fill="none"/></svg>
<svg class="abs gallery-arrow" style="left:622px" viewBox="0 0 14 24"><path d="M2 2l9 10-9 10" stroke="#fff" stroke-width="3.5" fill="none"/></svg>
<div class="abs gallery-caption">Lorem Ipsum is simply dummy text</div>

<footer>
  <div class="abs site-footer"></div>
  <div class="abs brand footer-brand"><span class="brand-dot"></span>Meridale Real Estate</div>
  <div class="abs footer-divider"></div>
  <ul class="abs footer-links" style="left:218px;top:1026px">
    <li>Home</li><li>Commercial</li><li>Residential</li><li>Farm</li><li>Vacant Land</li><li>Contact</li>
  </ul>
  <ul class="abs footer-links" style="left:311px;top:1026px">
    <li>Privacy Policy</li><li>Terms &amp; Conditions</li><li>Disclaimer</li><li>Legal Notice</li>
  </ul>
  <div class="abs contact" style="left:406px;top:1025px">
    <strong>Nora T. Vance</strong>nora@meridalehomes.com<br>(530) 555-0142<br>BRE#04417823
  </div>
  <div class="abs contact" style="left:406px;top:1086px">
    <strong style="margin-left:1px">Owen P. Marsh</strong>owen@meridalehomes.com<br>530.555.0187, 707.555.0163<br>BRE#05529104
  </div>
  <div class="abs connect" style="left:518px;top:1025px">
    <h4>Connect With Us</h4>
    <div class="social"><span></span><span></span><span></span><span></span><span></span></div>
  </div>
  <p class="abs copyright">© Copyrights 2015 Meridale Real Estate. All Right Reserved</p>
</footer>

</body>
</html>
```